Tall Fern Roofing Business Card

Need a business card with the logo that was designed here

Contact Information for Business Card

Name, Title, Phone, Email, Website, Company name

```html
<!DOCTYPE html>
<html lang="en">
<head>
<meta charset="utf-8">
<title>Tall Fern Roofing Business Card</title>
<link href="https://fonts.googleapis.com/css2?family=Montserrat:wght@400;500;700&display=swap" rel="stylesheet">
<style>
  :root {
    --brand-blue: #4174b9;
    --ink-grey: #555a60;
    --card-white: #ffffff;
    --stage: #d9d9d9;
  }
  * { margin: 0; padding: 0; box-sizing: border-box; }
  html, body { width: 1200px; height: 802px; overflow: hidden; }
  body {
    background: var(--stage);
    font-family: "Montserrat", sans-serif;
    position: relative;
  }
  .card {
    position: absolute;
    top: 246px;
    width: 540px;
    height: 309px;
    border-radius: 22px;
    overflow: hidden;
    box-shadow: 0 14px 30px rgba(0,0,0,0.22);
  }
  .card--front { left: 40px; background: var(--card-white); }
  .card--back { left: 620px; background: var(--brand-blue); }

  .front-band { position: absolute; inset: 0; width: 540px; height: 309px; }

  .wordmark {
    position: absolute;
    display: flex;
    align-items: center;
    gap: 10px;
    font-weight: 700;
    white-space: nowrap;
  }
  .wordmark__square { display: block; background: currentColor; }
  .wordmark--front {
    top: 38px; left: 250px;
    color: var(--brand-blue);
    font-size: 22px;
  }
  .wordmark--front .wordmark__square { width: 14px; height: 14px; }
  .wordmark--back {
    top: 50%; left: 50%;
    transform: translate(-50%, -50%);
    color: var(--card-white);
    font-size: 34px;
  }
  .wordmark--back .wordmark__square { width: 22px; height: 22px; }

  .person { position: absolute; left: 34px; top: 118px; }
  .person__name {
    color: var(--brand-blue);
    font-weight: 700;
    font-size: 21px;
    letter-spacing: 0.5px;
  }
  .person__title {
    color: var(--ink-grey);
    font-size: 12.5px;
    margin-top: 2px;
  }
  .contact { list-style: none; margin-top: 16px; }
  .contact__item {
    display: flex; align-items: center; gap: 8px;
    color: var(--ink-grey);
    font-size: 13px;
    line-height: 20px;
  }
  .contact__icon { width: 11px; height: 11px; flex: none; }

  .address {
    position: absolute;
    left: 34px; bottom: 12px;
    color: var(--card-white);
    font-size: 12.5px;
    font-weight: 500;
    letter-spacing: 0.3px;
  }
</style>
</head>
<body>

<section class="card card--front" aria-label="Card front">
  <svg class="front-band" viewBox="0 0 540 309" aria-hidden="true">
    <path d="M0 262 L392 262 L392 132 L462 66 L540 66 L540 309 L0 309 Z" fill="var(--brand-blue)"/>
    <path d="M0 269 L399 269 L399 135 L465 73 L540 73" fill="none" stroke="var(--card-white)" stroke-width="2.5"/>
  </svg>

  <div class="wordmark wordmark--front">
    <span class="wordmark__square"></span>
    <span class="wordmark__text">Tall Fern Roofing</span>
  </div>

  <div class="person">
    <h1 class="person__name">CORWIN MADDOX</h1>
    <p class="person__title">Managing Director</p>
    <ul class="contact">
      <li class="contact__item">
        <svg class="contact__icon" viewBox="0 0 12 12" aria-hidden="true"><path d="M2.5 1 L4.5 1 L5.2 3.6 L4 4.6 Q5 7 7.4 8 L8.4 6.8 L11 7.5 L11 9.5 Q11 11 9.5 11 Q1 10 1 2.5 Q1 1 2.5 1 Z" fill="var(--brand-blue)"/></svg>
        0491 555 217
      </li>
      <li class="contact__item">
        <svg class="contact__icon" viewBox="0 0 12 12" aria-hidden="true"><rect x="0.5" y="2" width="11" height="8" rx="1" fill="var(--brand-blue)"/><path d="M1 2.5 L6 6.5 L11 2.5" fill="none" stroke="#fff" stroke-width="1"/></svg>
        info@tallfernroofing.com
      </li>
      <li class="contact__item">
        <svg class="contact__icon" viewBox="0 0 12 12" aria-hidden="true"><circle cx="6" cy="6" r="5.5" fill="var(--brand-blue)"/><path d="M0.5 6 H11.5 M6 0.5 Q2.5 6 6 11.5 M6 0.5 Q9.5 6 6 11.5" fill="none" stroke="#fff" stroke-width="0.8"/></svg>
        www.tallfernroofing.com
      </li>
    </ul>
  </div>

  <p class="address">418 W Harlow Street Brenton County 6047</p>
</section>

<section class="card card--back" aria-label="Card back">
  <div class="wordmark wordmark--back">
    <span class="wordmark__square"></span>
    <span class="wordmark__text">Tall Fern Roofing</span>
  </div>
</section>

</body>
</html>
```